single page with calendar booking ability

a single web page that has the ability to book calendar times and dates, also needs to be able to link to my other business social media seamlessly. I don't want to get multiple developers and or agency's involved, I want you the web designer to design it and make sure it's up and works as described
. The boats we work on are between 20 feet to 40 feet, bow riders , cabin cruisers, and center consoles. The brands that we work on include but are not limited to Velmora, Praxen, Dunby Vale, Lark mil, Quilvane, Brevik, Drelo, and many more. Winterization and shrink wrapping is completely different than graphic wrapping, we do not do graphic's wrapping. Also, only 5% of our business will be auto detailing, the rest will be boats on trailers. Please ensure that the calendar booking system is intergraded and not a surprise to me later

Target Market(s)

Lakes region New Hampshire

Industry/Entity Type

marine

Coding

Coded - Design and coding required

Number of Pages Required

1 page

Colors
0054AA
0677BA
7BADD7
CADEEF
E8F1F8
00AB8E
00BBA5
67D7C9
C6EFE9
E9F9F6
EE7325
F08F49
F5BC92
FAE3D3
FDF4ED

Requirements
Must have
• calendar booking capability
Nice to have
• Pictures of boats being shrink wrapped for the winter season, Nice before and after pictures of boats detailed, only 5% of our business is auto detailing
Should not have
• Large yachts, lots of sail boats as we only do a few, graphics wrapping.. we don't graphic wrap

```html
<!DOCTYPE html>
<html lang="en">
<head>
<meta charset="utf-8">
<title>Lakeline Marine — Boat Services, Lakes Region NH</title>
<link href="https://fonts.googleapis.com/css2?family=Montserrat:wght@500;600;700;800&family=Open+Sans:wght@400;600&display=swap" rel="stylesheet">
<style>
:root{
  --blue:#0054AA;
  --blue-mid:#0677BA;
  --blue-soft:#7BADD7;
  --blue-pale:#CADEEF;
  --orange:#EE7325;
  --orange-soft:#F08F49;
  --ink:#1b1b1b;
  --text:#555;
  --grey-bg:#f1f1f1;
  --dark:#1f1f21;
  --darker:#151516;
  --white:#fff;
}
*{box-sizing:border-box;margin:0;padding:0}
html,body{width:1200px;height:4004px;overflow:hidden}
body{font-family:"Open Sans",Arial,sans-serif;color:var(--text);background:var(--white);position:relative}
h1,h2,h3,h4,.brand,.nav a,.btn{font-family:"Montserrat",Arial,sans-serif}
.btn{display:inline-block;background:var(--orange);color:var(--white);font-size:11px;font-weight:700;letter-spacing:.5px;padding:8px 16px;border-radius:2px;text-transform:uppercase}
.squiggle{display:block;margin:6px 0 18px}
.section-title{font-size:26px;font-weight:800;color:var(--ink);letter-spacing:.5px}
p{font-size:13px;line-height:1.7}

/* HERO */
.hero{position:absolute;left:0;top:0;width:1200px;height:640px;overflow:hidden}
.hero-photo{position:absolute;inset:0;background:linear-gradient(180deg,#8fb9dc 0%,#5d94c6 30%,#2f6fa8 55%,#17508a 75%,#0d3a6a 100%)}
.topbar{position:absolute;left:0;top:0;width:1200px;height:62px;display:flex;align-items:center;justify-content:space-between;padding:0 40px 0 24px}
.brand{display:flex;align-items:center;gap:10px;color:var(--white);font-weight:800;font-size:22px;letter-spacing:1px}
.brand .dot{width:34px;height:34px;border-radius:50%;background:var(--orange)}
.nav{display:flex;gap:28px}
.nav a{color:var(--white);font-size:11px;font-weight:700;text-decoration:none;letter-spacing:.5px}
.calendar{position:absolute;left:140px;top:185px;width:440px;height:360px;background:var(--white);box-shadow:0 6px 18px rgba(0,0,0,.25)}
.cal-head{padding:12px 18px;font-size:13px;color:var(--ink);border-bottom:1px solid #e3e3e3}
.cal-month{margin:12px 18px 6px;width:120px;border:1px solid #ccc;font-size:11px;padding:4px 8px;color:var(--ink)}
.cal-grid{display:grid;grid-template-columns:repeat(7,1fr);margin:6px 18px;row-gap:4px}
.cal-grid span{height:30px;display:flex;align-items:center;justify-content:center;font-size:11px;color:#444}
.cal-grid .dow{font-weight:600;color:#777;height:24px}
.cal-grid .sel{background:var(--blue-mid);color:var(--white);border-radius:50%;width:26px;height:26px;margin:2px auto}
.calendar .btn{position:absolute;right:16px;bottom:-14px}
.hero-copy{position:absolute;left:835px;top:176px;width:280px;color:var(--white)}
.hero-copy h1{font-size:26px;font-weight:800;color:var(--blue);letter-spacing:1px;margin-bottom:8px}
.hero-copy p{font-size:13px;line-height:1.5}
.dots{position:absolute;left:566px;top:574px;display:flex;gap:8px}
.dots i{width:8px;height:8px;border-radius:50%;background:rgba(255,255,255,.55)}
.dots i.on{background:var(--white)}
.hero-wave{position:absolute;left:0;bottom:0}

/* WELCOME */
.welcome{position:absolute;left:0;top:640px;width:1200px;height:512px}
.welcome-photo{position:absolute;left:130px;top:72px;width:476px;height:366px;background:linear-gradient(180deg,#9cc7ea 0%,#c9dce8 45%,#8a9b8a 70%,#5f6b62 100%)}
.welcome-copy{position:absolute;left:668px;top:74px;width:400px}
.welcome-copy h4{font-size:13px;font-weight:700;color:var(--ink);letter-spacing:1px}
.welcome-copy h2{font-size:26px;font-weight:800;color:var(--blue);letter-spacing:1px;margin-top:4px}
.welcome-copy .lead{font-size:15px;color:#333;margin-bottom:18px}

/* WHAT WE DO */
.whatwedo{position:absolute;left:0;top:1152px;width:1200px;height:568px;background:var(--grey-bg)}
.whatwedo-copy{position:absolute;left:130px;top:58px;width:560px}
.whatwedo-photo{position:absolute;right:0;top:0;width:460px;height:568px;background:radial-gradient(ellipse at 50% 55%,#2a3a4a 0%,#0e1a26 60%,#060b12 100%)}

/* STATS */
.stats{position:absolute;left:0;top:1720px;width:1200px;height:280px;background:var(--dark)}
.stats-wave{position:absolute;left:0;top:0}
.stat-row{position:absolute;left:130px;top:108px;width:940px;display:flex;justify-content:space-between}
.stat{width:260px;text-align:center;color:#ddd}
.stat h3{font-size:30px;font-weight:600;color:var(--white);margin-bottom:12px}
.stat p{font-size:12px;line-height:1.5;color:#bbb}

/* AUTO */
.auto{position:absolute;left:0;top:2000px;width:1200px;height:520px}
.auto-photo{position:absolute;left:130px;top:50px;width:462px;height:410px;background:linear-gradient(135deg,#222a33 0%,#3a4450 40%,#7a1f1f 75%,#b8342a 100%)}
.auto-copy{position:absolute;left:668px;top:70px;width:430px}

/* BLOG */
.blog{position:absolute;left:0;top:2520px;width:1200px;height:560px;background:var(--grey-bg)}
.blog .section-title{text-align:center;padding-top:52px}
.blog .squiggle{margin:6px auto 30px}
.cards{position:absolute;left:130px;top:148px;width:940px;display:flex;justify-content:space-between}
.card{width:298px;background:var(--white);height:360px}
.card-photo{height:178px}
.card-body{padding:18px 16px}
.card h4{font-size:13px;font-weight:800;color:var(--ink);line-height:1.4;margin-bottom:10px}
.card p{font-size:11px;line-height:1.6;margin-bottom:14px}

/* CONTACT */
.contact{position:absolute;left:0;top:3080px;width:1200px;height:540px;overflow:hidden}
.contact-photo{position:absolute;inset:0;background:linear-gradient(180deg,#0c1e33 0%,#163b5e 45%,#0e2a47 70%,#07121f 100%)}
.contact h2{position:absolute;left:0;top:96px;width:1200px;text-align:center;color:var(--white);font-size:24px;font-weight:800;letter-spacing:1px}
.contact .squiggle{position:absolute;left:588px;top:130px}
.form{position:absolute;left:270px;top:216px;width:660px;display:grid;grid-template-columns:1fr 1fr;gap:18px 14px}
.field{background:var(--white);height:34px;font-size:10px;color:#555;padding:10px 12px;text-transform:uppercase;font-weight:600}
.field.wide{grid-column:1/3;height:110px}
.form .btn{grid-column:1/3;justify-self:center;padding:9px 24px}

/* FOOTER */
.footer{position:absolute;left:0;top:3620px;width:1200px;height:384px;background:var(--darker);color:#ccc}
.footer .brand{position:absolute;left:130px;top:96px;font-size:26px}
.footer .brand .dot{width:40px;height:40px}
.fcol{position:absolute;top:92px}
.fcol h4{font-size:13px;font-weight:700;color:var(--white);margin-bottom:16px;letter-spacing:.5px}
.fcol ul{list-style:none}
.fcol li{font-size:11px;line-height:1.9;color:#bbb}
.fcol .row{display:flex;align-items:center;gap:12px;margin-bottom:14px;font-size:11px;line-height:1.4}
.icon{width:26px;height:26px;border-radius:50%;background:var(--white);flex:none;display:flex;align-items:center;justify-content:center}
.copyright{position:absolute;left:0;bottom:0;width:1200px;height:44px;border-top:1px solid #2c2c2e;text-align:center;font-size:10px;line-height:44px;color:#888}
</style>
</head>
<body>

<header class="hero">
  <div class="hero-photo" role="img" aria-label="Cabin cruiser under way on a blue lake with a cloudy sky"></div>
  <div class="topbar">
    <div class="brand"><span class="dot"></span>LAKELINE</div>
    <nav class="nav">
      <a>HOME</a><a>ABOUT US</a><a>WHAT WE DO</a><a>AUTO</a><a>BLOG</a><a>CONTACT US</a>
    </nav>
  </div>

  <div class="calendar">
    <div class="cal-head">14 Wednesday, 2021</div>
    <div class="cal-month">April 2021 ▾</div>
    <div class="cal-grid">
      <span class="dow">Sun</span><span class="dow">Mon</span><span class="dow">Tue</span><span class="dow">Wed</span><span class="dow">Thu</span><span class="dow">Fri</span><span class="dow">Sat</span>
      <span></span><span></span><span></span><span></span><span>1</span><span>2</span><span>3</span>
      <span>4</span><span>5</span><span>6</span><span>7</span><span>8</span><span>9</span><span>10</span>
      <span>11</span><span>12</span><span>13</span><span class="sel">14</span><span>15</span><span>16</span><span>17</span>
      <span>18</span><span>19</span><span>20</span><span>21</span><span>22</span><span>23</span><span>24</span>
      <span>25</span><span>26</span><span>27</span><span>28</span><span>29</span><span>30</span><span></span>
    </div>
    <a class="btn">Book</a>
  </div>

  <div class="hero-copy">
    <h1>BOATS&nbsp; SERVICES</h1>
    <p>Winterizing, shrink wrapping and detailing for boats from twenty to forty feet.</p>
  </div>

  <div class="dots"><i></i><i></i><i class="on"></i><i></i><i></i></div>

  <svg class="hero-wave" width="1200" height="90" viewBox="0 0 1200 90" aria-hidden="true">
    <path d="M0 40 C300 90 800 0 1200 50 L1200 90 L0 90 Z" fill="#0677BA" opacity=".7"/>
    <path d="M0 58 C320 100 820 20 1200 66 L1200 90 L0 90 Z" fill="#ffffff"/>
  </svg>
</header>

<section class="welcome">
  <div class="welcome-photo" role="img" aria-label="Cabin cruiser on a trailer in a driveway beside a house"></div>
  <div class="welcome-copy">
    <h4>WELCOME TO</h4>
    <h2>LAKELINE MARINE</h2>
    <svg class="squiggle" width="36" height="8" viewBox="0 0 36 8" aria-hidden="true"><path d="M1 4 Q5 0 9 4 T17 4 T25 4 T33 4" fill="none" stroke="#0054AA" stroke-width="2"/></svg>
    <p class="lead">We aim to run a company focused on providing customers in the lakes region of central New Hampshire with a broad range of premium boats and care services.</p>
    <p>We are on a mission to support boat and car owners to keep their vessels and cars clean, well maintained, protected and safe wherever they are at convenient prices.</p>
    <p style="margin-top:26px"><a class="btn">Read more</a></p>
  </div>
</section>

<section class="whatwedo">
  <div class="whatwedo-copy">
    <h2 class="section-title">WHAT WE DO</h2>
    <svg class="squiggle" width="36" height="8" viewBox="0 0 36 8" aria-hidden="true"><path d="M1 4 Q5 0 9 4 T17 4 T25 4 T33 4" fill="none" stroke="#0054AA" stroke-width="2"/></svg>
    <p>We aim to run a company focused on providing customers in the lakes region of central New Hampshire with a broad range of premium boat and care services, including but not limited to shrink wrap for boats, mobile detailing for boats and cars, mobile winterization for boats and much more. We already own a company operating a floating bar and restaurant on the lake and with a strong social media following we want to leverage our existing audience to deliver hundreds of thousands of views and interactions every day to nurture positive word of mouth and organic advertising. The lakes region market is extremely busy and with not so many competitors and no more dock spaces or yards available in the region we believe our services will be a great success, especially considering the steep growth in boat sales recently observed.</p>
    <p style="margin-top:24px"><a class="btn">Read more</a></p>
  </div>
  <div class="whatwedo-photo" role="img" aria-label="Aerial view of a white speedboat cutting across dark water"></div>
</section>

<section class="stats">
  <svg class="stats-wave" width="1200" height="60" viewBox="0 0 1200 60" aria-hidden="true">
    <path d="M0 0 L1200 0 L1200 10 C800 60 400 -10 0 40 Z" fill="#f1f1f1"/>
    <path d="M0 40 C400 -10 800 60 1200 10" fill="none" stroke="#0054AA" stroke-width="3"/>
  </svg>
  <div class="stat-row">
    <div class="stat"><h3>$73.91 B</h3><p>Marine services market<br>size in 2022.</p></div>
    <div class="stat"><h3>+4.70%</h3><p>compounded annual<br>growth until 2028</p></div>
    <div class="stat"><h3>$101.98 B</h3><p>forecasted marine services<br>market size within the<br>next seven years</p></div>
  </div>
</section>

<section class="auto">
  <div class="auto-photo" role="img" aria-label="Mechanic's hands working on a car engine with a wrench"></div>
  <div class="auto-copy">
    <h2 class="section-title">AUTO SERVICE</h2>
    <svg class="squiggle" width="36" height="8" viewBox="0 0 36 8" aria-hidden="true"><path d="M1 4 Q5 0 9 4 T17 4 T25 4 T33 4" fill="none" stroke="#0054AA" stroke-width="2"/></svg>
    <p>Alongside our boat work we offer a small range of auto care services for local customers. Our mobile team can come to your home, marina or workplace to wash, polish and protect your car, truck or tow vehicle, so it looks as good as the boat it pulls. We use the same careful products and methods that we trust on hulls and decks, and we take the time to treat every finish with respect. Interior cleaning, vacuuming, glass care and light paint correction are all available, and packages can be booked directly through the calendar above at a time that suits you. Auto detailing is a small part of what we do, but it gets the same attention to detail as everything else we offer.</p>
  </div>
</section>

<section class="blog">
  <h2 class="section-title">LATEST BLOG</h2>
  <svg class="squiggle" width="36" height="8" viewBox="0 0 36 8" aria-hidden="true"><path d="M1 4 Q5 0 9 4 T17 4 T25 4 T33 4" fill="none" stroke="#0054AA" stroke-width="2"/></svg>
  <div class="cards">
    <article class="card">
      <div class="card-photo" role="img" aria-label="Boat dashboard and helm controls" style="background:linear-gradient(135deg,#2b3a48,#6b7f90 55%,#b44a2a)"></div>
      <div class="card-body">
        <h4>WHEN TO BOOK YOUR WINTER SHRINK WRAP</h4>
        <p>Booking early keeps your boat protected before the first frost and frees your weekends for the last calm days on the lake.</p>
        <a class="btn">Read more</a>
      </div>
    </article>
    <article class="card">
      <div class="card-photo" role="img" aria-label="White bow rider cruising on open water" style="background:linear-gradient(180deg,#cfe2f2,#7badd7 50%,#2f6fa8)"></div>
      <div class="card-body">
        <h4>FIVE SIGNS YOUR HULL NEEDS A DETAIL</h4>
        <p>Chalky gelcoat, water lines and faded trim all point to a boat that would enjoy a deep clean and fresh layer of wax.</p>
        <a class="btn">Read more</a>
      </div>
    </article>
    <article class="card">
      <div class="card-photo" role="img" aria-label="Cabin cruiser running along a lake shoreline" style="background:linear-gradient(180deg,#e8f1f8,#9cc0de 45%,#0677BA)"></div>
      <div class="card-body">
        <h4>SPRING PREP FOR TRAILERED BOATS</h4>
        <p>A simple checklist for tires, bearings, lights and straps so your first launch of the season goes smoothly and safely.</p>
        <a class="btn">Read more</a>
      </div>
    </article>
  </div>
</section>

<section class="contact">
  <div class="contact-photo" role="img" aria-label="Boat on a dark lake at dusk"></div>
  <h2>CONTACT US</h2>
  <svg class="squiggle" width="36" height="8" viewBox="0 0 36 8" aria-hidden="true"><path d="M1 4 Q5 0 9 4 T17 4 T25 4 T33 4" fill="none" stroke="#ffffff" stroke-width="2"/></svg>
  <form class="form">
    <div class="field">First name</div>
    <div class="field">Last name</div>
    <div class="field">Email</div>
    <div class="field">Phone</div>
    <div class="field wide">Message</div>
    <a class="btn">Submit</a>
  </form>
</section>

<footer class="footer">
  <div class="brand"><span class="dot"></span>LAKELINE</div>
  <div class="fcol" style="left:480px">
    <h4>MENU</h4>
    <ul><li>HOME</li><li>ABOUT US</li><li>WHAT WE DO</li><li>AUTO</li><li>BLOG</li><li>CONTACT US</li></ul>
  </div>
  <div class="fcol" style="left:670px">
    <h4>CONTACT US</h4>
    <div class="row"><span class="icon"><svg width="12" height="14" viewBox="0 0 12 14"><path d="M6 0a5 5 0 0 0-5 5c0 4 5 9 5 9s5-5 5-9a5 5 0 0 0-5-5zm0 7a2 2 0 1 1 0-4 2 2 0 0 1 0 4z" fill="#151516"/></svg></span>48 Harbor Lane,<br>Gilford, NH 03249</div>
    <div class="row"><span class="icon"><svg width="12" height="12" viewBox="0 0 12 12"><path d="M2.5 0l2 2.5-1 1.5c.8 1.6 2 2.8 3.5 3.5l1.5-1L11 8.5 9.8 11C5 11 1 7 1 1.2z" fill="#151516"/></svg></span>Call Us<br>(603) 555-0142</div>
    <div class="row"><span class="icon"><svg width="12" height="10" viewBox="0 0 12 10"><rect x=".5" y=".5" width="11" height="9" fill="none" stroke="#151516"/><path d="M.5 .5L6 5.5 11.5 .5" fill="none" stroke="#151516"/></svg></span>E-mail Us<br>info@lakelinemarine.com</div>
  </div>
  <div class="fcol" style="left:900px">
    <h4>FOLLOW US</h4>
    <div class="row"><span class="icon"></span>Like us on<br>Our page</div>
    <div class="row"><span class="icon"></span>Follow us on<br>Our feed</div>
    <div class="row"><span class="icon"></span>Subscribe on<br>Our videos</div>
  </div>
  <div class="copyright">Copyright © 2021 All Rights Reserved.</div>
</footer>

</body>
</html>
```